Business card

We need a business card design for our company based in Auckland , New Zealand called 'Ridge + Studio Ltd'. We provide architectural services. We would like to see designs that use the max. three colours (such as white, black, grey) The final design should communicate financial safety and growth."
Also I will provide our company logo. I would like to the logo to be embeded onto our business card.

Target Market(s)

new residential house, alteration & addition & light commericila design & drafting service

Industry/Entity Type

Architecture

Contact Information for Business Card

Company name: ridge + studio Ltd.
Name: Mark Delford
Job title: architectural designer & Design LBP
email address: mark@rplusd.co.nz
mobile number: 02 5163 2290
web site: www.rplusd.co.nz

Requirements
Must have
• My project must have..
• - embeded logo (attached company logo)
• I don't have a bigger version for our company logo, but I have one old one, so you can remove the word from it)
• - insert the attached small BKTW logo & LBP logo
• - creative, simple and clear business card.
• - Max. three colours
Nice to have
• - Here are the samples I would like to share with you: http://www.plimvora.com/blog/minimalistic-business-card-designs/
• I would like to have my business card like one of the creation.
Should not have
• TBA

```html
<!DOCTYPE html>
<html lang="en">
<head>
<meta charset="utf-8">
<title>Ridge + Studio Ltd — Business Card</title>
<link rel="stylesheet" href="https://fonts.googleapis.com/css2?family=Tinos:wght@400;700&display=swap">
<style>
  :root {
    --stage: #d9d9d9;
    --paper: #ffffff;
    --ink: #0d0d0d;
    --grey: #6e6e6e;
    --soft-grey: #bdbdbd;
  }
  * { margin: 0; padding: 0; box-sizing: border-box; }
  html, body {
    width: 1200px;
    height: 950px;
    overflow: hidden;
    background: var(--stage);
    font-family: "Tinos", "Times New Roman", serif;
  }
  .canvas {
    position: relative;
    width: 1200px;
    height: 950px;
  }
  .card {
    position: absolute;
    left: 290px;
    width: 620px;
    height: 380px;
    background: var(--paper);
    overflow: hidden;
    box-shadow: 0 6px 18px rgba(0,0,0,0.18);
  }
  .card--back { top: 70px; }
  .card--front { top: 500px; }

  /* Back side */
  .affiliations {
    position: absolute;
    inset: 0;
    display: flex;
    align-items: center;
    justify-content: center;
    gap: 26px;
  }
  .affiliation-name {
    font-size: 46px;
    font-weight: 700;
    color: var(--grey);
    letter-spacing: 1px;
  }
  .affiliation-divider {
    width: 1px;
    height: 96px;
    background: var(--grey);
  }
  .lbp-badge {
    width: 96px;
    height: 96px;
    border-radius: 50%;
    background: var(--ink);
  }

  /* Front side */
  .front-shape {
    position: absolute;
    inset: 0;
  }
  .brand {
    position: absolute;
    left: 48px;
    top: 118px;
    display: flex;
    align-items: center;
    gap: 12px;
  }
  .brand-mark {
    width: 28px;
    height: 28px;
    border: 3px solid var(--ink);
    border-radius: 50%;
  }
  .brand-name {
    font-size: 28px;
    color: var(--ink);
  }
  .contact {
    position: absolute;
    left: 420px;
    top: 192px;
    width: 190px;
    color: var(--paper);
  }
  .contact-name {
    font-size: 22px;
    line-height: 1.1;
  }
  .contact-role {
    font-size: 17px;
    line-height: 1.15;
    margin-top: 2px;
  }
  .contact-company {
    font-size: 13px;
    margin-top: 10px;
  }
  .contact-list {
    list-style: none;
    margin-top: 4px;
    font-size: 13px;
  }
  .contact-list li {
    display: flex;
    align-items: center;
    gap: 7px;
    line-height: 1.4;
  }
  .contact-icon { width: 12px; height: 12px; flex: none; }
</style>
</head>
<body>
<main class="canvas">

  <section class="card card--back" aria-label="Business card back">
    <div class="affiliations">
      <span class="affiliation-name">BKTW</span>
      <span class="affiliation-divider"></span>
      <span class="lbp-badge" role="img" aria-label="Licensed practitioner badge"></span>
    </div>
  </section>

  <section class="card card--front" aria-label="Business card front">
    <svg class="front-shape" width="620" height="380" viewBox="0 0 620 380" aria-hidden="true">
      <rect width="620" height="380" fill="var(--ink)"/>
      <circle cx="120" cy="80" r="304" fill="var(--soft-grey)"/>
      <circle cx="120" cy="80" r="300" fill="var(--paper)"/>
    </svg>

    <div class="brand">
      <span class="brand-mark"></span>
      <span class="brand-name">Ridge + Studio Ltd</span>
    </div>

    <div class="contact">
      <p class="contact-name">Mark Delford</p>
      <p class="contact-role">architectural designer &amp;<br>Design LBP</p>
      <p class="contact-company">ridge + studio Ltd.</p>
      <ul class="contact-list">
        <li>
          <svg class="contact-icon" viewBox="0 0 13 13" aria-label="Mobile"><rect x="2.5" y="0.5" width="8" height="12" rx="1.2" fill="none" stroke="#fff" stroke-width="1.2"/></svg>
          02 5163 2290
        </li>
        <li>
          <svg class="contact-icon" viewBox="0 0 13 13" aria-label="Email"><rect x="0.5" y="2.5" width="12" height="8" fill="#fff"/><path d="M0.5 2.5 L6.5 7 L12.5 2.5" fill="none" stroke="#0d0d0d" stroke-width="1"/></svg>
          mark@rplusd.co.nz
        </li>
        <li>
          <svg class="contact-icon" viewBox="0 0 13 13" aria-label="Website"><circle cx="6.5" cy="6.5" r="6" fill="#fff"/><path d="M6.5 3 V6.5 H9.5" fill="none" stroke="#0d0d0d" stroke-width="1.2"/></svg>
          www.rplusd.co.nz
        </li>
      </ul>
    </div>
  </section>

</main>
</body>
</html>
```